House Cleaning Platform for Consumers and Cleaners

UPDATE: I've attached screenshots showing a purchase flow example, something all designers have missed in their designs. PLEASE check the URLs I've included in the brief for examples of a cleaning website. I've seen mostly landing pages and nothing else.

WHAT I'M LOOKING FOR:
I need the UI designed for a house cleaning web platform from 2 separate experiences: one from the consumer end to order a cleaner to come clean their house and one from a cleaner’s end that manages their orders and manages their schedule.

The UI will need to include photo uploading for before and after photos, a checkout/cart experience w/ tips, toggle options for adding and removing rooms/extras cleaning add-ons, customer+cleaner reviews (meaning the cleaner finished the job and they can rate and review the customer as well as the customer can rate and review the cleaner), order history for consumers, job history for cleaners, profile, settings, and landing pages for both.

PLEASE DO NOT USE THE COLOR BLUE AS THE PRIMARY COLOR. Use a light green (HEX #2fdf86) instead for primary theming color.

REFERENCES:
If you'd like a few websites I've enjoyed for references, checkout:
larkpolish.example, vomby.example, and brightfernhome.example.

For sake of branding, the company name is PlumNest. Currently do not have a logo as we have not decided on the name. Logo will come later.

Feel free to reach out to me if you have any questions!
Updates

Most designer submissions were a landing page and only a landing page. Very few designed the flows I requested and none designed a schedule management page. I even updated the Brief to more clearly outline the needs and references. Only about 2-3 of the designers actually did more than a landing page. Still don't believe I received 6 designers input that I had paid for.

Target Market(s)

FULL-TIME WORKING HOUSEHOLDS, SINGLE PROFESSIONALS, SINGLE PARENTS, ELDERLY & MOBILITY CHALLENGED, BUSY BODIES.

Industry/Entity Type

Cleaning, gig work.

Number of Pages Required

5+ page

Font styles to use
Other font styles liked:
• Jost or Lexend are great Google Font options I've used in the pitch deck and horribly done app mockups.

Colors
00AB8E
00BBA5
67D7C9
C6EFE9
E9F9F6
59FF00
82FF00
B8FF75
E3FFCB
F4FFEA
FFF300
FFF600
FEFA6F
FFFEC7
FFFEE8
FFC000
F8CF3A
FAE287
FDF2CF
FEFAEE

Requirements
Must have
• Landing page, consumer flow, cleaner schedule management, checkout flow, Rate & Review for consumer and/or cleaner, order history, profile.
Nice to have
• I'd like it to be simple in design and modern, but not so simple it's boring. Iconography can sometimes break that up, but I don't want it looking busy. It's a cleaning platform so the UI should look clean.

```html
<!DOCTYPE html>
<html lang="en">
<head>
<meta charset="utf-8">
<title>PlumNest – Booking Summary</title>
<link href="https://fonts.googleapis.com/css2?family=Catamaran:wght@500;600;700&family=Lexend:wght@300;400;500&display=swap" rel="stylesheet">
<style>
:root{
  --green:#2fdf86;
  --orange:#f7931e;
  --ink:#111;
  --body:#3a3a3a;
  --muted:#b9b9b9;
  --line:#d9d9d9;
  --bg:#fff;
  --grey-btn:#c9c9c9;
}
*{box-sizing:border-box;margin:0;padding:0}
html,body{width:1200px;height:3021px;overflow:hidden;background:var(--bg)}
body{position:relative;font-family:"Lexend",sans-serif;font-weight:300;color:var(--body);font-size:13px}
.abs{position:absolute}
/* header */
.brand{left:101px;top:18px;font-family:"Lexend",sans-serif;font-weight:500;font-size:30px;color:var(--green);letter-spacing:-.5px}
.nav{left:437px;top:27px;display:flex;gap:19px;font-size:12.5px;font-weight:400;color:var(--ink)}
.search{left:730px;top:22px;width:218px;height:25px;border:1px solid var(--line);border-radius:13px;display:flex;align-items:center;padding-left:10px;gap:12px;font-size:12px;font-weight:400;color:var(--ink)}
.login{left:979px;top:27px;font-size:12.5px;font-weight:400;color:var(--ink)}
.signup{left:1022px;top:22px;width:75px;height:25px;border-radius:13px;background:var(--green);color:var(--ink);font-size:11px;font-weight:400;display:flex;align-items:center;justify-content:center}
/* title */
.page-title{left:0;width:1200px;top:124px;text-align:center;font-family:"Catamaran",sans-serif;font-weight:700;font-size:42px;color:var(--ink)}
.stepper{left:160px;top:200px}
.rule{left:101px;width:1002px;height:1px;background:var(--line)}
/* summary */
.sum-title{font-family:"Catamaran",sans-serif;font-weight:500;font-size:22px;color:var(--ink)}
.price{font-family:"Catamaran",sans-serif;font-weight:700;font-size:33px;color:var(--orange)}
.old{font-family:"Catamaran",sans-serif;font-size:20px;color:#777;text-decoration:line-through}
.bullets{list-style:none;font-size:12px}
.bullets li{position:relative;padding-left:18px;height:24.5px}
.bullets li::before{content:"";position:absolute;left:0;top:5px;width:6px;height:6px;border-radius:50%;background:var(--ink)}
.vdiv{left:504px;top:309px;width:1px;height:125px;background:var(--line)}
/* sections */
.h2{font-family:"Catamaran",sans-serif;font-weight:600;font-size:22px;color:var(--ink);white-space:nowrap}
.h2 small{font-family:"Lexend",sans-serif;font-weight:300;font-size:11px;color:var(--muted);margin-left:10px}
.desc{font-size:11.5px;line-height:18px;color:var(--body)}
.desc b{font-weight:500;color:var(--ink)}
.field{height:37px;border:1px solid var(--line);border-radius:2px;display:flex;align-items:center;padding:0 18px;font-size:11.5px;color:var(--muted);justify-content:space-between}
.caret{width:0;height:0;border-left:6px solid transparent;border-right:6px solid transparent;border-top:7px solid var(--ink)}
.opt{height:37px;border:1px solid var(--line);border-radius:2px;display:flex;align-items:center;padding:0 18px;gap:12px;font-size:12px;font-weight:500;color:var(--ink)}
.opt .grow{flex:1}
.radio{width:13px;height:13px;border-radius:50%;border:1px solid #c8c8c8;flex:none}
.radio.on{border:3.5px solid var(--green)}
.help{width:13px;height:13px;border-radius:50%;border:1px solid #c8c8c8;font-size:8px;color:#bbb;display:flex;align-items:center;justify-content:center;font-weight:400}
.link{font-size:11.5px;color:var(--muted);font-weight:300}
.inline{display:flex;align-items:center;gap:12px;font-size:12px;font-weight:500;color:var(--ink)}
.italic{font-style:italic;font-weight:300;font-size:11.5px}
.orange-link{color:var(--orange);display:inline-flex;align-items:center;gap:8px;margin-left:12px}
.orange-link::before{content:"";width:5px;height:5px;border-radius:50%;background:var(--orange)}
.stepper-num{display:flex;border:1px solid var(--line);height:25px;margin-left:auto}
.stepper-num span{width:24px;display:flex;align-items:center;justify-content:center;font-weight:400;color:var(--ink);font-size:12px}
.stepper-num span+span{border-left:1px solid var(--line)}
.label{font-size:13px;font-weight:300;color:var(--ink);font-family:"Lexend",sans-serif}
.coupon{height:37px;border:1px solid var(--line);display:flex;align-items:center;justify-content:space-between;padding:0 18px;font-size:11.5px}
.apply{width:100px;height:25px;display:flex;align-items:center;justify-content:center;font-size:11.5px;font-weight:400;color:var(--ink);margin-right:-13px}
.btn{height:49px;width:174px;border-radius:25px;display:flex;align-items:center;justify-content:center;font-size:16px;font-weight:400;color:var(--ink)}
.btn.ghost{border:1px solid var(--line)}
.btn.primary{background:var(--green)}
.L{left:101px;width:466px}
.R{left:626px;width:467px}
</style>
</head>
<body>

<header>
  <div class="abs brand">PlumNest</div>
  <nav class="abs nav"><span>Home</span><span>Pricing</span><span>Services</span><span>Contact</span><span>Help</span></nav>
  <div class="abs search">
    <svg width="14" height="14" viewBox="0 0 14 14"><circle cx="6" cy="6" r="4.8" fill="none" stroke="#333" stroke-width="1.2"/><line x1="9.5" y1="9.5" x2="13" y2="13" stroke="#333" stroke-width="1.2"/></svg>
    <span>Search</span>
  </div>
  <div class="abs login">Login</div>
  <div class="abs signup">Sign Up</div>
</header>

<h1 class="abs page-title">Booking Summary</h1>

<svg class="abs stepper" width="880" height="28" viewBox="0 0 880 28" aria-hidden="true">
  <line x1="24" y1="14" x2="848" y2="14" stroke="#d3d3d3" stroke-width="2"/>
  <g fill="#fff" stroke="#cfcfcf" stroke-width="1.5">
    <circle cx="13" cy="14" r="11.5"/><circle cx="182" cy="14" r="11.5"/><circle cx="352" cy="14" r="11.5"/>
    <circle cx="521" cy="14" r="11.5"/><circle cx="860" cy="14" r="11.5"/>
  </g>
  <circle cx="691" cy="14" r="11.5" fill="#fff" stroke="#f7931e" stroke-width="2"/>
</svg>
<div class="abs rule" style="top:276px"></div>

<section>
  <div class="abs sum-title" style="left:101px;top:318px">First Clean</div>
  <div class="abs old" style="left:247px;top:320px">$350</div>
  <div class="abs price" style="left:300px;top:311px">$302.75</div>
  <ul class="abs bullets" style="left:101px;top:370px"><li>Deep Cleaning</li><li>Inside Fridge</li><li>Inside Oven</li></ul>
  <div class="abs vdiv"></div>
  <div class="abs sum-title" style="left:598px;top:318px">Recurring Cleans</div>
  <div class="abs price" style="left:799px;top:311px">$126.65</div>
  <ul class="abs bullets" style="left:598px;top:370px"><li>Standard Cleaning</li><li>Weekly</li><li>15% discount</li></ul>
</section>
<div class="abs rule" style="top:465px"></div>

<section>
  <h2 class="abs h2 L" style="top:529px">How Many Bedrooms?</h2>
  <p class="abs desc L" style="top:570px">Enter total number of bedrooms in the home. You can Exclude number of Bedrooms at a later step.</p>
  <div class="abs field L" style="top:625px"><span>Select Bedrooms</span><span class="caret"></span></div>
  <h2 class="abs h2 R" style="top:529px">How Many Bathrooms?</h2>
  <p class="abs desc R" style="top:570px">Enter total number of bathrooms in the home. <b>Round half baths up</b> (this will not affect price). You can Exclude Bedrooms at a later step.</p>
  <div class="abs field R" style="top:625px"><span>Select Bathhrooms</span><span class="caret"></span></div>
</section>

<section>
  <h2 class="abs h2 L" style="top:712px">Any Pets At Home?</h2>
  <p class="abs desc" style="left:101px;top:754px">This include any cats or dogs that live in or spend time in the same home. Select any one.</p>
  <div class="abs inline" style="left:101px;top:792px"><span class="radio on"></span>No pets in the home</div>
  <div class="abs inline" style="left:298px;top:792px"><span class="radio"></span>Dog(s)</div>
  <div class="abs inline" style="left:419px;top:792px"><span class="radio"></span>Cats(s)</div>
  <div class="abs inline" style="left:541px;top:792px"><span class="radio"></span>Dog(s) and Cats(s)</div>
</section>

<section>
  <h2 class="abs h2" style="left:101px;top:872px">Do You Want To Exclude Any Bathrooms Or Bedrooms?</h2>
  <p class="abs desc" style="left:101px;top:912px">If you don't need some rooms to cleaned, indicate that below. Excluding room will be calculated into the quote.</p>
  <div class="abs opt L" style="top:950px"><span class="radio on"></span>Exclude Bedroom(s)<div class="stepper-num"><span style="color:#bbb">−</span><span>1</span><span>+</span></div></div>
  <div class="abs opt R" style="top:950px"><span class="radio"></span>Exclude Bathroom(s)</div>
  <div class="abs opt L" style="top:1005px"><span class="radio"></span>Do not exclude any rooms</div>
</section>

<section>
  <h2 class="abs h2 L" style="top:1105px">Condition Of Home</h2>
  <p class="abs desc" style="left:101px;top:1146px">Select the condition that is most accurate. <span class="orange-link">View Condition guideline</span></p>
  <p class="abs desc" style="left:101px;top:1177px">Some home Conditions are not serviceable <span class="orange-link">View Excluded Condition</span></p>
  <div class="abs opt L" style="top:1214px"><span class="radio on"></span><span class="grow">Heavy dusty condition</span><span class="help">?</span></div>
  <div class="abs opt R" style="top:1214px"><span class="radio"></span><span class="grow">Average to Good condition</span><span class="help">?</span></div>
  <div class="abs opt L" style="top:1270px"><span class="radio"></span><span class="grow">Good to Great condition</span><span class="help">?</span></div>
  <div class="abs inline" style="left:101px;top:1340px"><span class="radio on"></span><span class="italic">I've read all the conditions carefully</span></div>
</section>

<section>
  <h2 class="abs h2 L" style="top:1419px">Type Of Cleaning</h2>
  <p class="abs desc" style="left:101px;top:1460px">View and compare cleaning checklists below. Please review the excluded services list as soon as not covered</p>
  <div class="abs opt L" style="top:1497px"><span class="radio on"></span><span class="grow">Deep Cleaning</span><span class="link">View Checklist</span></div>
  <div class="abs opt R" style="top:1497px"><span class="radio"></span><span class="grow">Move In/Out Cleaning</span><span class="link">View Checklist</span></div>
</section>

<section>
  <h2 class="abs h2 L" style="top:1597px">Add-On Services<small>(Optional)</small></h2>
  <p class="abs desc" style="left:101px;top:1639px">These services can be included in addition to the cleaning checklist</p>
  <div class="abs opt L" style="top:1676px"><span class="radio"></span><span class="grow">Inside Fridge</span><span class="help">?</span></div>
  <div class="abs opt R" style="top:1676px"><span class="radio"></span><span class="grow">Inside Cabinets</span><span class="help">?</span></div>
  <div class="abs opt L" style="top:1731px"><span class="radio"></span><span class="grow">Wipe Baseboard</span><span class="help">?</span></div>
  <div class="abs opt R" style="top:1731px"><span class="radio"></span><span class="grow">Inside Oven</span></div>
  <div class="abs opt L" style="top:1787px"><span class="radio"></span><span class="grow">Interior Windows</span><span class="help">?</span></div>
  <div class="abs opt R" style="top:1787px"><span class="radio"></span><span class="grow">Wet Wipe Blinds</span><span class="help">?</span></div>
  <div class="abs inline" style="left:101px;top:1858px"><span class="radio on"></span><span class="italic">I've read all the Checklists carefully</span></div>
</section>

<section>
  <h2 class="abs h2 L" style="top:1937px">Address Details</h2>
  <div class="abs label L" style="top:1986px">Property Address</div>
  <div class="abs field L" style="top:2017px">Property Address</div>
  <div class="abs label R" style="top:1986px">Apartment Or Suite #</div>
  <div class="abs field R" style="top:2017px">Apartment Or Suite #</div>
  <div class="abs label" style="left:101px;top:2074px">City</div>
  <div class="abs field" style="left:101px;width:291px;top:2105px">City</div>
  <div class="abs label" style="left:451px;top:2074px">State</div>
  <div class="abs field" style="left:451px;width:291px;top:2105px">State</div>
  <div class="abs label" style="left:801px;top:2074px">Zip Code</div>
  <div class="abs field" style="left:801px;width:292px;top:2105px">Zip Code</div>
  <div class="abs label" style="left:101px;top:2162px">Notes Or Special Instructions?</div>
  <div class="abs field" style="left:101px;width:992px;top:2193px;height:111px;align-items:flex-start;padding-top:12px">Notes Or Special Instructions?</div>
</section>

<section>
  <h2 class="abs h2 L" style="top:2368px">Contact Information</h2>
  <div class="abs label L" style="top:2417px">First Name</div>
  <div class="abs field L" style="top:2449px">First Name</div>
  <div class="abs label R" style="top:2417px">Last Name</div>
  <div class="abs field R" style="top:2449px">Last Name</div>
  <div class="abs label L" style="top:2505px">Email</div>
  <div class="abs field L" style="top:2536px">Email</div>
  <div class="abs label R" style="top:2505px">Phone</div>
  <div class="abs field R" style="top:2536px">Phone</div>
</section>

<section>
  <h2 class="abs h2 L" style="top:2593px">Other Details</h2>
  <div class="abs label L" style="top:2641px">How Did You Hear About Us?</div>
  <div class="abs field" style="left:101px;width:992px;top:2672px"><span>How Did You Hear About Us?</span><span class="caret"></span></div>
  <div class="abs label L" style="top:2730px">Enter Coupon Code</div>
  <div class="abs coupon L" style="top:2761px"><span style="color:var(--ink);font-weight:400">12345</span><span class="apply" style="background:var(--orange)">Apply</span></div>
  <div class="abs label R" style="top:2730px">Enter Coupon Code</div>
  <div class="abs coupon R" style="top:2761px"><span style="color:var(--muted)">Enter Coupon Code</span><span class="apply" style="background:var(--grey-btn);color:#fff">Apply</span></div>
</section>

<div class="abs btn ghost" style="left:101px;top:2860px">Back</div>
<div class="abs btn primary" style="left:305px;top:2860px">Make Payment</div>

</body>
</html>
```